New manufacturing IT architecture concept powerpoint presentation

Create an appealing PowerPoint presentation, from handmade sketches, to illustrate a new approach to manufacturing IT architectures. We want to present the idea to augment the experience of people working in manufacturing plants using AI based on the data that our systems normally collect. We even want to present the power of having a tier 2 Manufacturing execution system that can coordinate and optimize production between multiple plants of the same corporate. The target audience is IT managers, Operations Managers, plant managers, engineering managers, and Continuous improvement managers.
Target Market(s)
Manufacturing companies mostly in Food & Bev and CPG. Mostly big multinational companies
Industry/Entity Type
Software manufacturing solutions (MES/MOM)
Font styles to use
Other font styles liked:
- Segoe
Look and feel

```html
<!DOCTYPE html>
<html lang="en">
<head>
<meta charset="utf-8">
<title>NEXA OPS – Manufacturing IT Architecture</title>
<link rel="stylesheet" href="https://fonts.googleapis.com/css2?family=Roboto:wght@400;500;700&family=Roboto+Condensed:wght@700&display=swap">
<style>
:root{
  --page:#e8e9eb;
  --navy:#0d2a4a;
  --deep:#0a1a2e;
  --blue:#1b6fc1;
  --teal:#2bb3b1;
  --teal-dark:#1f8e8b;
  --ink:#1d1d1f;
  --grey:#5b5f66;
  --panel:#eceef1;
  --red:#d6102a;
  --chart-blue:#123e7c;
  --white:#ffffff;
}
*{box-sizing:border-box;margin:0;padding:0}
html,body{width:1200px;height:4051px;overflow:hidden}
body{background:var(--page);font-family:"Roboto",Arial,sans-serif;color:var(--ink);position:relative}
.slide{position:absolute;left:77px;width:1047px;height:588px;overflow:hidden;background:var(--white);box-shadow:0 6px 18px rgba(0,0,0,.12)}
.brand{position:absolute;right:59px;top:30px;font-family:"Roboto Condensed",Arial,sans-serif;font-weight:700;font-size:46px;letter-spacing:1px;color:var(--blue)}
.brand.light{color:var(--white)}
.slide-heading{position:absolute;left:60px;top:32px;font-size:19px;font-weight:700;color:var(--ink)}
.heading-rule{position:absolute;left:0;top:75px;width:708px;height:5px;background:var(--teal)}
.fill{position:absolute;display:block}

/* cover */
.cover{top:88px;background:linear-gradient(120deg,#1b4a6e 0%,#163b5c 40%,#0e2b46 70%,#07162a 100%)}
.cover .title{position:absolute;left:60px;top:228px;color:var(--white);font-size:28px;font-weight:700;line-height:45px}

/* technology */
.tech{top:738px}
.tech .title{position:absolute;left:621px;top:238px;font-size:26px;font-weight:700}
.tech .lead{position:absolute;left:621px;top:290px;width:380px;font-size:17px;line-height:29px;color:var(--grey)}

/* challenges */
.challenges{top:1397px}
.challenges .intro{position:absolute;left:60px;top:122px;font-size:19px;font-weight:500}
.challenge-list{list-style:none;position:absolute;left:60px;top:168px;width:470px}
.challenge-list li{position:relative;height:82px;display:flex;align-items:center;padding-left:92px;font-size:17px;line-height:26px;color:var(--grey)}
.challenge-list .icon{position:absolute;left:0;top:9px;width:64px;height:64px;border-radius:50%;background:var(--white);box-shadow:0 2px 8px rgba(0,0,0,.15);display:flex;align-items:center;justify-content:center}
.challenges .visual{left:576px;top:135px;width:410px;height:382px;background:linear-gradient(135deg,#2e5c9c,#3f8fe0 45%,#0e2f66)}

/* activity */
.activity{top:2056px;background:var(--panel)}
.activity svg{position:absolute;left:0;top:0}
.node-label{font-family:"Roboto",Arial,sans-serif;font-size:14px;font-weight:700;fill:var(--ink)}

/* chart */
.turnover{top:2715px;background:linear-gradient(100deg,#ffffff 40%,#e4f0f8 75%,#d6e9f5)}
.turnover svg{position:absolute;left:0;top:0}
.axis-label{font-family:"Roboto",Arial,sans-serif;font-size:11px;fill:#444}
.legend{position:absolute;top:549px;display:flex;align-items:center;font-size:17px}
.legend i{display:inline-block;width:62px;height:22px;margin-right:16px}

/* closing */
.closing{top:3374px;background:linear-gradient(135deg,#1c2c3c,#0c1622)}
.closing .thanks{position:absolute;left:0;width:100%;top:232px;text-align:center;color:var(--white);font-size:80px;font-weight:700;letter-spacing:1px}
.contact{position:absolute;top:489px;display:flex;align-items:center;color:var(--white);font-size:16px;line-height:23px}
.contact .dot{width:62px;height:62px;border-radius:50%;background:var(--white);display:flex;align-items:center;justify-content:center;margin-right:28px;box-shadow:0 0 0 5px rgba(255,255,255,.25)}
</style>
</head>
<body>

<section class="slide cover">
  <div class="fill" role="img" aria-label="Hands holding a tablet surrounded by floating hexagonal technology icons" style="inset:0;background:radial-gradient(circle at 72% 45%,rgba(120,170,220,.55),transparent 45%)"></div>
  <svg class="fill" style="left:0;top:0" width="1047" height="588" viewBox="0 0 1047 588">
    <polygon points="0,0 110,0 0,100" fill="#ffffff"/>
    <polygon points="125,0 140,0 0,128 0,113" fill="var(--teal)"/>
    <polygon points="0,128 140,0 150,0 17,125 17,588 0,588" fill="var(--teal)"/>
  </svg>
  <div class="brand light">NEXA OPS</div>
  <h1 class="title">UNIFIED OPERATION CENTER &amp;<br>AUGMENTED OPERATION<br>MANAGEMENT</h1>
</section>

<section class="slide tech">
  <svg class="fill" style="left:0;top:0" width="1047" height="588" viewBox="0 0 1047 588">
    <defs>
      <linearGradient id="techPhoto" x1="0" y1="0" x2="1" y2="1">
        <stop offset="0" stop-color="#9fb3c6"/>
        <stop offset=".5" stop-color="#5f7f99"/>
        <stop offset="1" stop-color="#1d3550"/>
      </linearGradient>
    </defs>
    <polygon role="img" aria-label="Two people wearing VR headsets over a holographic city model" points="0,0 672,0 395,588 0,588" fill="url(#techPhoto)"/>
    <polygon points="672,0 686,0 408,588 395,588" fill="var(--blue)"/>
    <polygon points="640,115 654,115 440,588 418,588" fill="var(--teal)"/>
  </svg>
  <div class="brand">NEXA OPS</div>
  <h2 class="title">OUR TECHNOLOGY</h2>
  <p class="lead">How digitalization evolved in last years from being technology focused to user and value focused</p>
</section>

<section class="slide challenges">
  <h2 class="slide-heading">SUBJECT MATTTER EXPERT</h2>
  <div class="heading-rule"></div>
  <div class="brand">NEXA OPS</div>
  <p class="intro">Main challenged companies face today:</p>
  <ul class="challenge-list">
    <li><span class="icon"><svg width="30" height="30" viewBox="0 0 30 30" fill="none" stroke="#1b6fc1" stroke-width="2"><circle cx="15" cy="15" r="11"/><path d="M15 22v-8M15 14c-4 0-5-3-5-5 3 0 5 1 5 5zM15 14c4 0 5-3 5-5-3 0-5 1-5 5z"/></svg></span>Sustainability</li>
    <li><span class="icon"><svg width="30" height="30" viewBox="0 0 30 30" fill="none" stroke="#1b6fc1" stroke-width="2"><path d="M15 4l10 6v10l-10 6-10-6V10z M5 10l10 6 10-6 M15 16v10"/></svg></span>Flexibility ⟶ availability of assets, experience (SMEs), decisions</li>
    <li><span class="icon"><svg width="30" height="30" viewBox="0 0 30 30" fill="none" stroke="#1b6fc1" stroke-width="2"><circle cx="15" cy="15" r="10"/><circle cx="15" cy="15" r="4"/><path d="M15 2v4M15 24v4M2 15h4M24 15h4"/></svg></span>Workforce demographic ⟶ experience, decisions</li>
    <li><span class="icon"><svg width="30" height="30" viewBox="0 0 30 30" fill="none" stroke="#1b6fc1" stroke-width="2"><rect x="4" y="6" width="22" height="18"/><circle cx="15" cy="15" r="3"/><path d="M9 10l3 3M21 10l-3 3M9 20l3-3M21 20l-3-3"/></svg></span>Corporate wide visibility and coordination</li>
    <li><span class="icon"><svg width="30" height="30" viewBox="0 0 30 30" fill="none" stroke="#1b6fc1" stroke-width="2"><circle cx="15" cy="15" r="10"/><path d="M11 11h5v5h-5zM15 15h5v5h-5z"/><path d="M5 15l-2-3M25 15l2 3"/></svg></span>Supply Chain visibility and coordination</li>
  </ul>
  <div class="fill visual" role="img" aria-label="Glowing digital gear interface over people working at a desk"></div>
</section>

<section class="slide activity">
  <svg width="1047" height="588" viewBox="0 0 1047 588">
    <defs>
      <radialGradient id="globe" cx=".5" cy=".6" r=".6">
        <stop offset="0" stop-color="#f3c46a"/>
        <stop offset=".35" stop-color="#5a5a5a"/>
        <stop offset="1" stop-color="#0b0b0b"/>
      </radialGradient>
      <filter id="lift" x="-30%" y="-30%" width="160%" height="160%"><feDropShadow dx="0" dy="2" stdDeviation="3" flood-opacity=".2"/></filter>
    </defs>
    <g fill="none" stroke="var(--teal-dark)" stroke-width="1.5">
      <circle cx="522" cy="290" r="132"/>
      <polyline points="321,139 391,139 441,186"/>
      <polyline points="723,139 653,139 603,186"/>
      <line x1="321" y1="291" x2="390" y2="291"/>
      <line x1="723" y1="291" x2="654" y2="291"/>
      <polyline points="321,443 391,443 441,392"/>
      <polyline points="723,443 653,443 603,392"/>
      <line x1="522" y1="422" x2="522" y2="458"/>
    </g>
    <g fill="var(--panel)" stroke="var(--teal-dark)" stroke-width="1.5">
      <circle cx="441" cy="186" r="5"/><circle cx="603" cy="186" r="5"/>
      <circle cx="390" cy="291" r="5"/><circle cx="654" cy="291" r="5"/>
      <circle cx="441" cy="392" r="5"/><circle cx="603" cy="392" r="5"/>
      <circle cx="522" cy="422" r="5"/>
    </g>
    <circle role="img" aria-label="Hands holding a glowing globe" cx="522" cy="290" r="110" fill="url(#globe)"/>
    <g fill="#ffffff" filter="url(#lift)">
      <circle cx="286" cy="139" r="35"/><circle cx="286" cy="291" r="35"/><circle cx="286" cy="443" r="35"/>
      <circle cx="758" cy="139" r="35"/><circle cx="758" cy="291" r="35"/><circle cx="758" cy="443" r="35"/>
      <circle cx="522" cy="493" r="35"/>
    </g>
    <g fill="none" stroke="var(--blue)" stroke-width="2.2">
      <circle cx="286" cy="139" r="13"/><circle cx="286" cy="139" r="5"/>
      <circle cx="286" cy="291" r="4"/><path d="M276 281l20 20M296 281l-20 20"/><circle cx="275" cy="280" r="3"/><circle cx="297" cy="280" r="3"/><circle cx="275" cy="302" r="3"/><circle cx="297" cy="302" r="3"/>
      <circle cx="286" cy="436" r="5"/><path d="M273 455a13 13 0 0 1 26 0"/><circle cx="272" cy="438" r="3"/><circle cx="300" cy="438" r="3"/>
      <rect x="748" y="126" width="20" height="20" rx="4"/><path d="M748 138h20M752 152l-4 4M764 152l4 4"/>
      <circle cx="758" cy="291" r="14"/><path d="M758 287v10M758 282v1"/>
      <rect x="748" y="432" width="20" height="24" rx="2"/><circle cx="758" cy="443" r="5"/>
      <rect x="510" y="487" width="15" height="15"/><rect x="518" y="481" width="15" height="15"/>
    </g>
    <text class="node-label" x="228" y="144" text-anchor="end">SKILL</text>
    <text class="node-label" x="228" y="296" text-anchor="end">CONNECT</text>
    <text class="node-label" x="228" y="448" text-anchor="end">COORDINATE</text>
    <text class="node-label" x="818" y="144">TRAIN</text>
    <text class="node-label" x="818" y="296">INFORM</text>
    <text class="node-label" x="818" y="448">AUGMENT</text>
    <text class="node-label" x="522" y="558" text-anchor="middle">UNIFY</text>
  </svg>
  <h2 class="slide-heading">OUR ACTIVITY</h2>
  <div class="heading-rule"></div>
  <div class="brand">NEXA OPS</div>
</section>

<section class="slide turnover">
  <svg width="1047" height="588" viewBox="0 0 1047 588">
    <g stroke="#d9dde2" stroke-width="1">
      <line x1="104" y1="176" x2="953" y2="176"/>
      <line x1="104" y1="223.5" x2="953" y2="223.5"/>
      <line x1="104" y1="271" x2="953" y2="271"/>
      <line x1="104" y1="318.5" x2="953" y2="318.5"/>
      <line x1="104" y1="366" x2="953" y2="366"/>
      <line x1="104" y1="413.5" x2="953" y2="413.5"/>
      <line x1="104" y1="461" x2="953" y2="461" stroke="#9aa0a6"/>
    </g>
    <g class="axis-label" text-anchor="end">
      <text x="96" y="180">6</text><text x="96" y="227">5</text><text x="96" y="275">4</text>
      <text x="96" y="322">3</text><text x="96" y="370">2</text><text x="96" y="417">1</text><text x="96" y="465">0</text>
    </g>
    <g class="axis-label" text-anchor="middle">
      <text x="171" y="482">t1</text><text x="253" y="482">t2</text><text x="335" y="482">t3</text>
      <text x="417" y="482">t4</text><text x="499" y="482">t5</text><text x="580" y="482">t6</text>
      <text x="664" y="482">t7</text><text x="745" y="482">t8</text><text x="827" y="482">t9</text><text x="909" y="482">t10</text>
    </g>
    <polyline fill="none" stroke="var(--red)" stroke-width="1.8" points="104,340 190,340 363,314 442,314 536,326 623,307 780,240 867,224 945,197"/>
    <polyline fill="none" stroke="var(--chart-blue)" stroke-width="1.8" points="104,352 190,352 277,340 363,318 442,280 521,262 607,254 694,231 780,219 867,193 945,183"/>
  </svg>
  <h2 class="slide-heading">WORKFORCE TURNOVER ⟶ MISSING EXPERIENCE</h2>
  <div class="heading-rule"></div>
  <div class="brand">NEXA OPS</div>
  <div class="legend" style="left:332px"><i style="background:var(--red)"></i>Knowledge</div>
  <div class="legend" style="left:546px"><i style="background:var(--chart-blue)"></i>Experience</div>
</section>

<section class="slide closing">
  <div class="fill" role="img" aria-label="Engineer working on machinery with hexagonal technology icons" style="inset:0;background:radial-gradient(circle at 40% 55%,rgba(90,110,130,.5),transparent 55%)"></div>
  <svg class="fill" style="left:0;top:0" width="1047" height="588" viewBox="0 0 1047 588">
    <polygon points="459,0 1047,0 1047,588 745,588" fill="var(--teal-dark)" opacity=".93"/>
  </svg>
  <div class="brand light">NEXA OPS</div>
  <div class="thanks">THANK YOU</div>
  <div class="contact" style="left:89px">
    <span class="dot"><svg width="26" height="26" viewBox="0 0 24 24" fill="var(--teal)"><path d="M12 2a7 7 0 0 0-7 7c0 5 7 13 7 13s7-8 7-13a7 7 0 0 0-7-7zm0 9.5A2.5 2.5 0 1 1 12 6.5a2.5 2.5 0 0 1 0 5z"/></svg></span>
    <span>465, Lorum Ipsum Dolore,<br>United States</span>
  </div>
  <div class="contact" style="left:431px">
    <span class="dot"><svg width="24" height="24" viewBox="0 0 24 24" fill="var(--teal)"><path d="M6.6 10.8a15 15 0 0 0 6.6 6.6l2.2-2.2c.3-.3.7-.4 1-.2 1.1.4 2.3.6 3.6.6.6 0 1 .4 1 1V20c0 .6-.4 1-1 1A17 17 0 0 1 3 4c0-.6.4-1 1-1h3.5c.6 0 1 .4 1 1 0 1.3.2 2.5.6 3.6.1.3 0 .7-.2 1z"/></svg></span>
    <span>+1 (888) 888 8888</span>
  </div>
  <div class="contact" style="left:727px">
    <span class="dot"><svg width="24" height="24" viewBox="0 0 24 24" fill="var(--teal)"><path d="M3 5h18v14H3z" /><path d="M3 6l9 7 9-7" fill="none" stroke="#fff" stroke-width="1.8"/></svg></span>
    <span>info@nexaops.com</span>
  </div>
</section>

</body>
</html>
```